Business Card for Professional Photographer

I'm looking for an eye catching modern clean design that compliments my logo/ website fonts & colours.
I specialise in architecture, corporate & commercial photography so I'm marketing to professional clients rather than portrait / wedding clients.

I would prefer to not have a solid black design.

My logo brand guide is as follows :

Main front font. : Reislust
Main font colour : #fff
Slogan front font : Ubuntu Bold
Monogram front font : Venti Medium
Container colour : #fff

I need print ready files in pdf .png & .eps formats.

Included in the files below are some screen grabs as reference to font & colours etc.

```html
<!DOCTYPE html>
<html lang="en">
<head>
<meta charset="utf-8">
<title>Angle North – Business Card</title>
<link rel="stylesheet" href="https://fonts.googleapis.com/css2?family=Ubuntu:wght@300;400;500;700&family=Roboto:wght@400&display=swap">
<style>
  :root {
    --backdrop: #3b3b3c;
    --card: #1d1d1f;
    --card-deep: #131315;
    --gold: #c99a3e;
    --gold-light: #e6c277;
    --ink: #f2f2f2;
    --tile-1: #2b3240;
    --tile-2: #3a3128;
    --tile-3: #2a3038;
    --tile-4: #352c24;
    --tile-5: #30363c;
    --tile-6: #3b352f;
    --veil: rgba(12, 12, 14, .55);
  }
  * { box-sizing: border-box; margin: 0; padding: 0; }
  html, body { width: 799px; height: 1200px; overflow: hidden; }
  body {
    background: var(--backdrop);
    font-family: "Ubuntu", sans-serif;
    position: relative;
  }
  .card {
    position: absolute;
    left: 60px;
    width: 680px;
    height: 410px;
    border-radius: 4px;
    overflow: hidden;
    box-shadow: 0 14px 30px rgba(0,0,0,.45);
  }
  .card--front { top: 150px; background: var(--card-deep); }
  .card--back { top: 660px; background: linear-gradient(135deg, var(--card) 0%, var(--card-deep) 100%); }

  /* Front: photo collage grid */
  .photo-collage {
    position: absolute; inset: 0;
    display: grid;
    grid-template-columns: 30% 30% 40%;
    grid-template-rows: 32% 36% 32%;
    gap: 3px;
  }
  .photo-tile { display: block; }
  .photo-tile--interior { background: linear-gradient(160deg, var(--tile-1), #1c2028); grid-column: 1; grid-row: 1; }
  .photo-tile--water { background: linear-gradient(180deg, var(--tile-3), #181c22); grid-column: 1; grid-row: 2 / 4; }
  .photo-tile--office { background: linear-gradient(150deg, var(--tile-2), #221d18); grid-column: 2; grid-row: 1 / 3; }
  .photo-tile--product { background: linear-gradient(170deg, var(--tile-4), #1e1a16); grid-column: 2; grid-row: 3; }
  .photo-tile--facade { background: linear-gradient(200deg, var(--tile-5), #1a1e23); grid-column: 3; grid-row: 1 / 3; }
  .photo-tile--gallery { background: linear-gradient(140deg, var(--tile-6), #201c19); grid-column: 3; grid-row: 3; }
  .collage-veil { position: absolute; inset: 0; background: var(--veil); }

  .logo-square {
    width: 96px; height: 96px;
    border: 5px solid var(--gold);
    border-radius: 14px;
  }
  .front-brand {
    position: absolute; left: 140px; top: 70px;
    display: flex; align-items: flex-end; gap: 18px;
  }
  .front-brand .logo-square { width: 108px; height: 108px; }
  .brand-text { display: flex; flex-direction: column; }
  .brand-name {
    color: var(--gold);
    font-family: "Ubuntu", sans-serif;
    font-weight: 400;
    font-size: 34px;
    letter-spacing: 5px;
    text-transform: uppercase;
    line-height: 1;
  }
  .brand-slogan {
    color: var(--gold);
    font-family: "Ubuntu", sans-serif;
    font-weight: 700;
    font-size: 11.5px;
    letter-spacing: 2.2px;
    margin-top: 7px;
  }
  .front-web {
    position: absolute; left: 140px; top: 275px;
    color: var(--gold-light);
    font-size: 20px;
    letter-spacing: 4px;
  }

  /* Back */
  .back-brand {
    position: absolute; left: 30px; top: 95px; width: 290px;
    display: flex; flex-direction: column; align-items: center;
  }
  .back-brand .logo-square { width: 118px; height: 118px; margin-bottom: 20px; }
  .back-brand .brand-name { font-size: 26px; letter-spacing: 4px; }
  .back-brand .brand-slogan { font-size: 9px; letter-spacing: 1.5px; margin-top: 6px; }
  .divider {
    position: absolute; left: 330px; top: 60px;
    width: 2px; height: 290px;
    background: linear-gradient(180deg, transparent, var(--gold-light) 20%, var(--gold) 80%, transparent);
  }
  .contact { position: absolute; left: 365px; top: 110px; color: var(--ink); font-family: "Roboto", sans-serif; }
  .contact-name { color: var(--gold); font-family: "Ubuntu", sans-serif; font-weight: 700; font-size: 24px; }
  .contact-role { font-size: 18px; margin-top: 2px; }
  .contact-list { list-style: none; margin-top: 26px; font-size: 18px; line-height: 28px; }
  .contact-list li { display: flex; align-items: center; gap: 12px; }
  .contact-list svg { width: 16px; height: 16px; fill: var(--gold); flex: none; }
  .contact-address { font-size: 18px; line-height: 28px; }
</style>
</head>
<body>
  <section class="card card--front">
    <div class="photo-collage">
      <span class="photo-tile photo-tile--interior" role="img" aria-label="Photograph of a modern interior"></span>
      <span class="photo-tile photo-tile--water" role="img" aria-label="Photograph of a waterfront scene"></span>
      <span class="photo-tile photo-tile--office" role="img" aria-label="Photograph of a corporate office"></span>
      <span class="photo-tile photo-tile--product" role="img" aria-label="Commercial product photograph"></span>
      <span class="photo-tile photo-tile--facade" role="img" aria-label="Photograph of a white building facade"></span>
      <span class="photo-tile photo-tile--gallery" role="img" aria-label="Photograph of a gallery wall"></span>
    </div>
    <div class="collage-veil"></div>
    <div class="front-brand">
      <div class="logo-square"></div>
      <div class="brand-text">
        <span class="brand-name">Angle North</span>
        <span class="brand-slogan">Architecture Corporate Commercial</span>
      </div>
    </div>
    <div class="front-web">www.anglenorth.com.au</div>
  </section>

  <section class="card card--back">
    <div class="back-brand">
      <div class="logo-square"></div>
      <span class="brand-name">Angle North</span>
      <span class="brand-slogan">Architecture Corporate Commercial</span>
    </div>
    <div class="divider"></div>
    <div class="contact">
      <div class="contact-name">Owen Hartley</div>
      <div class="contact-role">Photographer</div>
      <ul class="contact-list">
        <li>
          <svg viewBox="0 0 16 16" aria-hidden="true"><path d="M3 1h3l1 4-2 1a9 9 0 0 0 5 5l1-2 4 1v3c0 1-1 2-2 2A13 13 0 0 1 1 3c0-1 1-2 2-2z"/></svg>
          0400555218
        </li>
        <li>
          <svg viewBox="0 0 16 16" aria-hidden="true"><path d="M1 3h14v10H1z M2 4l6 5 6-5" fill="none" stroke="#c99a3e" stroke-width="1.4"/></svg>
          hello@anglenorth.com.au
        </li>
        <li>
          <svg viewBox="0 0 16 16" aria-hidden="true"><g fill="none" stroke="#c99a3e" stroke-width="1.3"><circle cx="8" cy="8" r="6.5"/><ellipse cx="8" cy="8" rx="3" ry="6.5"/><path d="M1.5 8h13"/></g></svg>
          www.anglenorth.com.au
        </li>
      </ul>
      <div class="contact-address">48 Ridge Rd Ashwell Vic 3999</div>
    </div>
  </section>
</body>
</html>
```